KELBRIDGE PAINTING

We are a painting company. We paint residential, commercial and strata jobs. I need the website to be very sharp, neat and elegant. I've attached our logo. the Logo needs to be embossed as a gold color and the background like a Matt black. I need these tabs:

• HOME • ABOUT US • SERVICES • TESTIMONIALS • SHOWCASE • CONTACT US

Be creative and innovative in your style.
take this as an example to just get the gist of what I'm expecting. If you can better it then the job is yours!

http://rickhalvorpainting.com.au/contact.html

I look forward to seeing your artwork :)

#These are the links to my logo in PSD format.

https://www.filevaultzy.com/s/qwertplk83nd7ha/Kelbridge%20Painting%20Luxury%20Gold.rar

https://www.filevaultzy.com/sh/bzuyrak2m5wqp9/QoPL7-xvMn

Painting

• Making the Logo embossed like the artworks i have attached is definitely a necessity.

Can you let me know if this is possible to apply to the website.

thank you

```html
<!DOCTYPE html>
<html lang="en">
<head>
<meta charset="utf-8">
<title>Kelbridge Painting — Testimonials</title>
<link rel="stylesheet" href="https://fonts.googleapis.com/css2?family=Source+Sans+3:ital,wght@0,400;0,600;0,700;1,400&display=swap">
<style>
  :root {
    --matt-black: #1d222b;
    --panel: #1e232c;
    --footer: #454a52;
    --gold: #f0c050;
    --gold-deep: #d4a21c;
    --gold-mid: #e5b440;
    --gold-soft: #f0c45a;
    --sand: #f5d7a0;
    --slate-1: #4a4f57;
    --slate-2: #6b6f76;
    --slate-3: #9a9a9a;
    --white: #ffffff;
    --ink: #1d222b;
  }
  * { box-sizing: border-box; margin: 0; padding: 0; }
  html, body { width: 1114px; height: 1200px; overflow: hidden; background: var(--panel); }
  body { font-family: "Source Sans 3", sans-serif; color: var(--white); position: relative; }

  .site-header { position: absolute; left: 0; top: 0; width: 1114px; height: 86px; background: var(--matt-black); border-bottom: 1px solid var(--gold-deep); z-index: 3; }
  .phone { position: absolute; left: 806px; top: 18px; display: flex; align-items: center; gap: 8px; color: var(--gold); font-weight: 700; font-size: 20px; letter-spacing: 0.3px; }
  .main-nav { position: absolute; top: 60px; left: 398px; display: flex; gap: 28px; }
  .main-nav a { color: var(--white); text-decoration: none; font-weight: 700; font-size: 13px; letter-spacing: 0.8px; text-transform: uppercase; }
  .main-nav a.is-active { color: var(--gold); }

  .brand-disc { position: absolute; left: 157px; top: 20px; width: 106px; height: 106px; border-radius: 50%; background: var(--matt-black); z-index: 4; }
  .brand-ribbon { position: absolute; left: 257px; top: 87px; width: 471px; height: 36px; background: linear-gradient(90deg, #e8b640, #f6d77a 45%, #e9bb4a); display: flex; align-items: center; padding-left: 16px; z-index: 4; }
  .brand-name { font-weight: 700; font-size: 21px; letter-spacing: 1.6px; color: var(--ink); }
  .brand-divider { width: 1px; height: 18px; background: var(--gold-deep); margin: 0 13px; }
  .brand-tagline { font-style: italic; font-size: 17px; color: var(--ink); }

  .hero { position: absolute; left: 0; top: 87px; width: 1114px; height: 419px; background: linear-gradient(180deg, #6e5443 0%, #8a6a55 35%, #a8836a 62%, #c8ab95 100%); }
  .slider-dots { position: absolute; top: 115px; left: 900px; display: flex; gap: 9px; z-index: 2; }
  .slider-dots span { width: 8px; height: 8px; background: #3a3d44; }
  .slider-dots span.is-current { background: var(--gold); }

  .hero-caption { position: absolute; left: 153px; top: 311px; width: 618px; height: 148px; z-index: 2; }
  .hero-caption .corner-tl { position: absolute; left: 0; top: 0; width: 53px; height: 52px; background: var(--gold-mid); }
  .hero-caption .corner-br { position: absolute; left: 464px; top: 53px; width: 154px; height: 95px; background: var(--gold-mid); }
  .hero-caption .box { position: absolute; left: 10px; top: 10px; width: 591px; height: 128px; background: var(--matt-black); padding: 16px 0 0 33px; }
  .hero-caption .tab { position: absolute; left: 569px; top: 10px; width: 32px; height: 6px; background: var(--slate-3); }
  .hero-caption h1 { font-weight: 400; font-size: 41px; line-height: 47px; color: var(--white); }

  .stripe { position: absolute; left: 0; width: 1114px; height: 8px; display: flex; }
  .stripe span { height: 100%; }
  .stripe-top { top: 506px; }
  .stripe-bottom { top: 1131px; height: 9px; }

  .testimonials { position: absolute; left: 153px; top: 514px; width: 810px; }
  .testimonials h2 { position: absolute; top: 34px; font-weight: 700; font-size: 42px; color: var(--gold); white-space: nowrap; }
  .quote { position: absolute; width: 236px; }
  .quote p { font-size: 13.5px; line-height: 25.7px; color: var(--white); }
  .quote cite { display: block; text-align: right; font-style: normal; font-weight: 600; font-size: 17px; color: var(--gold-mid); margin-top: 18px; }

  .site-footer { position: absolute; left: 0; top: 1140px; width: 1114px; height: 60px; background: var(--footer); }
  .copyright { position: absolute; left: 155px; top: 19px; font-size: 11.5px; color: var(--white); }
  .social { position: absolute; left: 802px; top: 16px; display: flex; gap: 15px; }
  .social span { width: 28px; height: 28px; border-radius: 50%; background: #8a8c90; }
  .social span.is-blue { background: #2f5aa8; }
</style>
</head>
<body>

<header class="site-header">
  <div class="phone">
    <svg width="18" height="18" viewBox="0 0 24 24" aria-hidden="true"><path fill="#f0c050" d="M6.6 10.8a15.1 15.1 0 0 0 6.6 6.6l2.2-2.2c.3-.3.7-.4 1-.2 1.1.4 2.3.6 3.6.6.6 0 1 .4 1 1V20c0 .6-.4 1-1 1A17 17 0 0 1 3 4c0-.6.4-1 1-1h3.5c.6 0 1 .4 1 1 0 1.3.2 2.5.6 3.6.1.3 0 .7-.2 1z"/></svg>
    <span>1300 47 19 52</span>
  </div>
  <nav class="main-nav">
    <a class="is-active" href="#">Home</a>
    <a href="#">About Us</a>
    <a href="#">Services</a>
    <a href="#">Testimonials</a>
    <a href="#">Showcase</a>
    <a href="#">Contact Us</a>
  </nav>
</header>

<div class="brand-disc"></div>
<div class="brand-ribbon">
  <span class="brand-name">KELBRIDGE PAINTING</span>
  <span class="brand-divider"></span>
  <span class="brand-tagline">Painting Australia Everyday!</span>
</div>

<section class="hero" role="img" aria-label="Warm-toned living room with a brown and cream leather corner sofa">
  <div class="slider-dots"><span></span><span></span><span></span><span class="is-current"></span></div>
  <div class="hero-caption">
    <div class="corner-tl"></div>
    <div class="corner-br"></div>
    <div class="box"><h1>We paint residential,<br>commercial and strata jobs</h1></div>
    <div class="tab"></div>
  </div>
</section>

<div class="stripe stripe-top">
  <span style="width:267px;background:var(--matt-black)"></span>
  <span style="width:76px;background:var(--slate-1)"></span>
  <span style="width:84px;background:var(--slate-2)"></span>
  <span style="width:132px;background:var(--slate-3)"></span>
  <span style="width:111px;background:var(--gold-deep)"></span>
  <span style="width:77px;background:var(--gold-mid)"></span>
  <span style="width:84px;background:var(--gold-soft)"></span>
  <span style="width:283px;background:var(--sand)"></span>
</div>

<main class="testimonials">
  <h2>Testimonials</h2>

  <blockquote class="quote" style="left:0;top:128px">
    <p>Lorem ipsum dolor sit amet, consectetur adipiscing elit. Quantum Aristoxeni ingenium consumptum videmus in musicis? Nihil enim hoc differt. Re mihi non aeque satisfacit, et quidem locis pluribus.</p>
    <cite>Client Name</cite>
  </blockquote>
  <blockquote class="quote" style="left:276px;top:128px">
    <p>Lorem ipsum dolor sit amet, consectetur adipiscing elit. Quantum Aristoxeni ingenium consumptum videmus in musicis? Nihil enim hoc differt. Re mihi non aeque satisfacit, et quidem locis pluribus.</p>
    <cite>Client Name</cite>
  </blockquote>
  <blockquote class="quote" style="left:551px;top:128px">
    <p>Lorem ipsum dolor sit amet, consectetur adipiscing elit. Quantum Aristoxeni ingenium consumptum videmus in musicis? Nihil enim hoc differt. Re mihi non aeque satisfacit, et quidem locis pluribus.</p>
    <cite>Client Name</cite>
  </blockquote>

  <blockquote class="quote" style="left:0;top:368px">
    <p>Lorem ipsum dolor sit amet, consectetur adipiscing elit. Quantum Aristoxeni ingenium consumptum videmus in musicis? Nihil enim hoc differt. Re mihi non aeque satisfacit, et quidem locis pluribus.</p>
    <cite>Client Name</cite>
  </blockquote>
  <blockquote class="quote" style="left:276px;top:368px">
    <p>Lorem ipsum dolor sit amet, consectetur adipiscing elit. Quantum Aristoxeni ingenium consumptum videmus in musicis? Nihil enim hoc differt. Re mihi non aeque satisfacit, et quidem locis pluribus.</p>
    <cite>Client Name</cite>
  </blockquote>
  <blockquote class="quote" style="left:551px;top:368px">
    <p>Lorem ipsum dolor sit amet, consectetur adipiscing elit. Quantum Aristoxeni ingenium consumptum videmus in musicis? Nihil enim hoc differt. Re mihi non aeque satisfacit, et quidem locis pluribus.</p>
    <cite>Client Name</cite>
  </blockquote>
</main>

<div class="stripe stripe-bottom">
  <span style="width:284px;background:var(--sand)"></span>
  <span style="width:84px;background:var(--gold-soft)"></span>
  <span style="width:76px;background:var(--gold-mid)"></span>
  <span style="width:113px;background:var(--gold-deep)"></span>
  <span style="width:130px;background:var(--slate-3)"></span>
  <span style="width:84px;background:var(--slate-2)"></span>
  <span style="width:77px;background:var(--slate-1)"></span>
  <span style="width:266px;background:var(--footer)"></span>
</div>

<footer class="site-footer">
  <p class="copyright">Copyright @ 2013 Kelbridge Painting. All rights reserved.</p>
  <div class="social">
    <span class="is-blue" role="img" aria-label="Linkora"></span>
    <span role="img" aria-label="Chirpwave"></span>
    <span role="img" aria-label="Circlenet"></span>
    <span role="img" aria-label="Pinboardly"></span>
  </div>
</footer>

</body>
</html>
```